Paraffin Wax Packaging Design for Nail and Beauty Industry

We need an attractive design for the packaging of our new product, Paraffin Wax. Our company is a wholesale beauty/nail supply company that has been selling to nail salons in the US market for 10 years. We currently sell this product that we buy from another company. Now we want to launch our own brand of Paraffin Wax.

Target Market(s)

Retail nail salons in the US market.

Industry/Entity Type

Industry

Font styles to use
Sans Serif

Colors

Designer to choose colors to be used in the design.

Requirements
Must have
• Our logo (attached).
• All information on the "Ingredient List" (attached).
• Design for Clear Packaging so product can show through.
• Design for Package Dimensions of 4.25" x 11" (110cm x 280 cm).
Nice to have
• Picture related to women's skin and or beauty.
• Contrast as in the design of product that we currently sell (attached).

```html
<!DOCTYPE html>
<html lang="en">
<head>
<meta charset="utf-8">
<title>By Marelle Paraffin Wax Packaging</title>
<link rel="stylesheet" href="https://fonts.googleapis.com/css2?family=Libre+Baskerville:wght@400;700&family=Italianno&family=Arimo:wght@400&display=swap">
<style>
  :root {
    --page-bg: #e9e9ec;
    --label-white: #ffffff;
    --ink: #111111;
    --script-violet: #3b3596;
    --band-light: #4d72d8;
    --band-deep: #3e3e9c;
    --band-text: #ffffff;
    --photo-light: #f3ebe6;
    --photo-mid: #e4d3c8;
    --photo-dark: #cdb8ab;
  }
  * { box-sizing: border-box; margin: 0; padding: 0; }
  html, body {
    width: 1200px;
    height: 2400px;
    overflow: hidden;
    background: var(--page-bg);
  }
  .package-label {
    position: absolute;
    left: 171px;
    top: 86px;
    width: 857px;
    height: 2223px;
    background: var(--label-white);
    overflow: hidden;
    font-family: "Libre Baskerville", "Times New Roman", serif;
    color: var(--ink);
    text-align: center;
  }
  .brand-name {
    position: absolute;
    top: 110px;
    left: 0;
    width: 100%;
    font-weight: 700;
    font-size: 96px;
    line-height: 1;
    color: var(--ink);
  }
  .product-name {
    position: absolute;
    top: 352px;
    left: 0;
    width: 100%;
    font-family: "Italianno", cursive;
    font-weight: 400;
    font-size: 168px;
    line-height: 1;
    color: var(--script-violet);
  }
  .compatibility {
    position: absolute;
    top: 588px;
    left: 0;
    width: 100%;
    font-weight: 700;
    font-size: 46px;
    line-height: 69px;
  }
  .benefit {
    position: absolute;
    top: 833px;
    left: 0;
    width: 100%;
    font-size: 28px;
    line-height: 41px;
  }
  .ingredients {
    position: absolute;
    top: 948px;
    left: 0;
    width: 100%;
  }
  .ingredients-title {
    font-weight: 700;
    font-size: 20px;
    line-height: 30px;
  }
  .ingredients-list {
    font-size: 19px;
    line-height: 29px;
    margin-top: 4px;
  }
  .hero-photo {
    position: absolute;
    left: 60px;
    top: 1090px;
    width: 760px;
    height: 790px;
  }
  .wave-band {
    position: absolute;
    left: 0;
    top: 1860px;
    width: 857px;
    height: 363px;
  }
  .caution {
    position: absolute;
    top: 2018px;
    left: 0;
    width: 100%;
    font-family: "Arimo", Arial, sans-serif;
    font-size: 25px;
    line-height: 32px;
    color: var(--band-text);
  }
  .net-weight {
    position: absolute;
    top: 2141px;
    left: 0;
    width: 100%;
    font-family: "Arimo", Arial, sans-serif;
    font-size: 34px;
    line-height: 44px;
    color: var(--band-text);
  }
</style>
</head>
<body>
  <main class="package-label">
    <div class="brand-name">By Marelle</div>

    <h1 class="product-name">Paraffin Wax</h1>

    <p class="compatibility">Compatible For Use With<br>Most Wax Paraffin<br>Heat Therapy Units.</p>

    <p class="benefit">Deeply Moisturizes the Skin Restoring a<br>Healthier Look and Feel to Skin.</p>

    <section class="ingredients">
      <h2 class="ingredients-title">Ingredients:</h2>
      <p class="ingredients-list">Paraffin waxes and Hydrocarbon waxes, Petrolatum, Paraffin oils,<br>Apricot kernel oil, Fragrance D &amp; C dyes.</p>
    </section>

    <svg class="hero-photo" role="img" aria-label="Photo of a seated woman in white underwear hugging her knees, with a white lily in her dark hair" viewBox="0 0 760 790" preserveAspectRatio="none">
      <defs>
        <linearGradient id="photoTone" x1="0" y1="0" x2="1" y2="1">
          <stop offset="0%" stop-color="var(--photo-light)"/>
          <stop offset="55%" stop-color="var(--photo-mid)"/>
          <stop offset="100%" stop-color="var(--photo-dark)"/>
        </linearGradient>
      </defs>
      <rect width="760" height="790" fill="url(#photoTone)"/>
    </svg>

    <svg class="wave-band" viewBox="0 0 857 363" preserveAspectRatio="none" aria-hidden="true">
      <defs>
        <linearGradient id="bandTone" x1="0" y1="0" x2="1" y2="0">
          <stop offset="0%" stop-color="var(--band-light)"/>
          <stop offset="100%" stop-color="var(--band-deep)"/>
        </linearGradient>
      </defs>
      <path d="M0 40 C 220 0, 520 0, 857 70 L 857 363 L 0 363 Z" fill="url(#bandTone)"/>
    </svg>

    <p class="caution">Caution:<br>Paraffin is flammable. Do not use near<br>open flame or an unprotected resistance heater.</p>

    <p class="net-weight">Net Wt. 1 lb. (450 g.)</p>
  </main>
</body>
</html>
```